Commercial Real Estate

We need a business card design for a new commercial real estate business that specializes in apartment building brokerage. Not individual units but the entire complex. We find and represent the owners existing buildings and well as new buyers for those buildings. The design should convey trust, integrity, knowledge and growth. It should be easily read.

Target Market(s)

40 to 65 years old

Industry/Entity Type

Real Estate

```html
<!DOCTYPE html>
<html lang="en">
<head>
<meta charset="utf-8">
<title>Kestrel Estates – Business Card</title>
<link rel="stylesheet" href="https://fonts.googleapis.com/css2?family=Open+Sans:wght@400;600;700&display=swap">
<style>
  :root {
    --page-bg: #e6e7e9;
    --card-bg: #ffffff;
    --card-bg-soft: #f3f4f5;
    --teal: #69c0c3;
    --slate: #4b5056;
    --ink: #2f3338;
    --shadow: rgba(0, 0, 0, 0.22);
  }
  * { margin: 0; padding: 0; box-sizing: border-box; }
  html, body {
    width: 1038px;
    height: 1200px;
    overflow: hidden;
    background: var(--page-bg);
    font-family: "Open Sans", Arial, sans-serif;
  }
  .sheet {
    position: relative;
    width: 1038px;
    height: 1200px;
  }
  .card {
    position: absolute;
    left: 79px;
    width: 880px;
    height: 500px;
    background: linear-gradient(160deg, var(--card-bg) 40%, var(--card-bg-soft) 100%);
    box-shadow: 0 6px 18px var(--shadow);
    overflow: hidden;
  }
  .card--front { top: 60px; }
  .card--back  { top: 640px; }

  /* brand name block */
  .brand {
    position: absolute;
    left: 70px;
    top: 300px;
    display: flex;
    align-items: center;
    gap: 16px;
  }
  .brand__mark {
    width: 30px;
    height: 30px;
    background: var(--teal);
  }
  .brand__name {
    font-size: 38px;
    font-weight: 700;
    color: var(--slate);
    letter-spacing: 0.5px;
  }

  /* contact block */
  .contact {
    position: absolute;
    right: 63px;
    top: 168px;
    text-align: right;
    color: var(--ink);
  }
  .contact__name {
    font-size: 22px;
    font-weight: 700;
    color: var(--teal);
    line-height: 30px;
  }
  .contact__title {
    font-size: 19px;
    line-height: 28px;
    margin-bottom: 30px;
  }
  .contact__list { list-style: none; }
  .contact__item {
    display: flex;
    justify-content: flex-end;
    align-items: center;
    gap: 12px;
    font-size: 18px;
    line-height: 27.5px;
  }
  .contact__icon {
    width: 16px;
    height: 16px;
    flex: none;
  }
  .contact__address {
    font-size: 18px;
    line-height: 27.5px;
    margin-top: 6px;
    padding-right: 28px;
  }

  .card__band {
    position: absolute;
    left: 0;
    bottom: 0;
    width: 880px;
    height: 50px;
  }
</style>
</head>
<body>
<main class="sheet">

  <section class="card card--front" aria-label="Business card front">
    <div class="brand">
      <span class="brand__mark"></span>
      <span class="brand__name">Kestrel Estates</span>
    </div>

    <div class="contact">
      <p class="contact__name">Daniel Ashcombe</p>
      <p class="contact__title">Technical Director</p>
      <ul class="contact__list">
        <li class="contact__item">03 9000 4182
          <svg class="contact__icon" viewBox="0 0 16 16" aria-hidden="true"><path d="M4 1.5 L6.5 4.5 L5 6.2 C6 8.4 7.6 10 9.8 11 L11.5 9.5 L14.5 12 L12.8 14.4 C7 14 2 9 1.6 3.2 Z" fill="var(--teal)"/></svg>
        </li>
        <li class="contact__item">0400 315 862
          <svg class="contact__icon" viewBox="0 0 16 16" aria-hidden="true"><rect x="3.5" y="1" width="9" height="14" rx="1.5" fill="none" stroke="var(--teal)" stroke-width="1.8"/><circle cx="8" cy="12.3" r="1" fill="var(--teal)"/></svg>
        </li>
        <li class="contact__item">daniel@kestrelestates.com.au
          <svg class="contact__icon" viewBox="0 0 16 16" aria-hidden="true"><circle cx="8" cy="8" r="7.5" fill="var(--teal)"/><rect x="4" y="5.5" width="8" height="5.5" fill="#fff"/><path d="M4 5.5 L8 8.6 L12 5.5" fill="none" stroke="var(--teal)" stroke-width="1"/></svg>
        </li>
        <li class="contact__item">www.kestrelestates.com.au
          <svg class="contact__icon" viewBox="0 0 16 16" aria-hidden="true"><circle cx="8" cy="8" r="7.5" fill="var(--teal)"/><circle cx="8" cy="8" r="4" fill="none" stroke="#fff" stroke-width="1.2"/><path d="M4 8 H12 M8 4 V12" stroke="#fff" stroke-width="1"/></svg>
        </li>
      </ul>
      <p class="contact__address">Level 2, 18 Carrow Ln, Australia Sydney</p>
    </div>

    <svg class="card__band" viewBox="0 0 880 50" aria-hidden="true">
      <rect x="0" y="6" width="450" height="10" fill="var(--slate)"/>
      <path d="M880 0 H450 C436 0 432 4 426 12 L420 22 V50 H880 Z" fill="var(--teal)"/>
    </svg>
  </section>

  <section class="card card--back" aria-label="Business card back"></section>

</main>
</body>
</html>
```